Hair Salon Brochure/ Menu

Double sided salon menu / brochure (non folding). Targeting young professionals. Color theme of salon is pink, white, grey & black. Please make sure the dollar amount is aligned properly.

Target Market(s)

Professionals, college students & girls.

Industry/Entity Type

Beauty Salon

Font styles to use
Decorative
Script

Colors
ffffff
eea4c8
9d9d9d
333333

Requirements
Must have
• Black (can fade from black to grey- from top to bottom) background on both sides (double-sided), White font for services, pink logo & graphics.
Nice to have
• Nice finishing graphics around borders or frame.

```html
<!DOCTYPE html>
<html lang="en">
<head>
<meta charset="utf-8">
<title>Tresslane Salon Menu</title>
<link href="https://fonts.googleapis.com/css2?family=Lato:wght@300;400&family=Raleway:wght@500;700;800&family=Roboto:ital,wght@0,300;0,400;1,300&display=swap" rel="stylesheet">
<style>
:root{
  --stage:#161616;
  --sheet-top:#1c1c1c;
  --sheet-bottom:#3b3b3b;
  --violet:#a64bd2;
  --pink:#eea4c8;
  --white:#ffffff;
  --grey:#9d9d9d;
  --label:#d6d6d6;
  --leader:#8a8a8a;
}
*{margin:0;padding:0;box-sizing:border-box}
html,body{width:1200px;height:1015px;overflow:hidden;background:var(--stage)}
.canvas{position:relative;width:1200px;height:1015px}
.side-label{position:absolute;font-family:"Lato",sans-serif;font-weight:300;font-size:38px;color:var(--label);transform:translateX(-50%);white-space:nowrap;letter-spacing:.5px}
.sheet{position:absolute;top:110px;width:546px;height:825px;background:linear-gradient(to bottom,var(--sheet-top),var(--sheet-bottom))}
.sheet.front{left:38px}
.sheet.back{left:609px;width:542px}
.frame{position:absolute;left:12px;top:12px;right:12px;bottom:12px;border:4px solid;border-image:linear-gradient(to bottom,var(--violet),var(--pink)) 1}
.corner{position:absolute;width:28px;height:28px;background:var(--violet);opacity:.4}
.corner.bottom{background:var(--pink)}
.brand-rule{position:absolute;height:3px;background:var(--violet)}
.brand-name{position:absolute;left:0;right:0;text-align:center;font-family:"Raleway",sans-serif;font-weight:500;font-size:52px;color:var(--violet);letter-spacing:4px;line-height:1}
.section-title{position:absolute;left:0;right:0;text-align:center;font-family:"Raleway",sans-serif;font-weight:800;font-size:17.5px;color:var(--pink);line-height:1;letter-spacing:.3px}
.title-rule{position:absolute;left:50%;transform:translateX(-50%);width:76px;height:5px;border-top:1px solid var(--pink);border-bottom:1px solid var(--pink);opacity:.7}
.menu-row{position:absolute;display:grid;grid-template-columns:16px auto 1fr 52px;align-items:end;font-family:"Roboto",sans-serif;font-weight:300;font-size:10.8px;color:var(--white);line-height:1;white-space:nowrap}
.menu-row svg{width:12px;height:12px}
.leader{border-bottom:1.5px dotted var(--leader);margin:0 10px 2px 3px;height:1px}
.price{text-align:left}
.note{position:absolute;font-family:"Roboto",sans-serif;font-style:italic;font-weight:300;font-size:8.6px;color:var(--white);white-space:nowrap}
.decor{position:absolute;width:62px;height:64px;border-radius:6px;background:linear-gradient(135deg,rgba(238,164,200,.5),rgba(238,164,200,.15))}
.contact{position:absolute;left:0;right:0;text-align:center;font-family:"Raleway",sans-serif;font-weight:700;font-size:13.5px;color:var(--white);letter-spacing:3.2px;line-height:1;white-space:nowrap}
.contact.address{font-size:12.5px;letter-spacing:2.2px}
.contact.back-web{font-size:12.5px;letter-spacing:3px}
</style>
</head>
<body>
<svg width="0" height="0" style="position:absolute">
  <defs>
    <symbol id="scissors" viewBox="0 0 12 12">
      <circle cx="3" cy="9.5" r="1.6" fill="none" stroke="#eea4c8" stroke-width="1"/>
      <circle cx="6" cy="10" r="1.6" fill="none" stroke="#eea4c8" stroke-width="1"/>
      <line x1="4" y1="8.3" x2="11" y2="1" stroke="#eea4c8" stroke-width="1"/>
      <line x1="5.5" y1="8.5" x2="9" y2="1.5" stroke="#eea4c8" stroke-width="1"/>
    </symbol>
  </defs>
</svg>
<main class="canvas">
  <div class="side-label" style="left:318px;top:38px">FRONT SIDE</div>
  <div class="side-label" style="left:892px;top:50px">BACK SIDE</div>

  <section class="sheet front">
    <div class="frame"></div>
    <div class="corner" role="img" aria-label="Corner fretwork ornament" style="left:24px;top:24px"></div>
    <div class="corner" role="img" aria-label="Corner fretwork ornament" style="right:24px;top:24px"></div>
    <div class="corner bottom" role="img" aria-label="Corner fretwork ornament" style="left:24px;bottom:24px"></div>
    <div class="corner bottom" role="img" aria-label="Corner fretwork ornament" style="right:24px;bottom:24px"></div>

    <div class="brand-rule" style="left:56px;width:427px;top:53px"></div>
    <div class="brand-name" style="top:62px">TRESSLANE</div>
    <div class="brand-rule" style="left:56px;width:427px;top:122px"></div>

    <div class="title-rule" style="top:149px"></div>
    <h2 class="section-title" style="top:157px">SEW-INS / WEAVES</h2>
    <div class="title-rule" style="top:181px"></div>

    <div class="menu-row" style="left:32px;width:487px;top:207px"><svg><use href="#scissors"/></svg><span>SIGNATURE/ PARTIAL</span><span class="leader"></span><span class="price">$65</span></div>
    <div class="menu-row" style="left:32px;width:487px;top:225px"><svg><use href="#scissors"/></svg><span>GRAND/ FULL</span><span class="leader"></span><span class="price">$90</span></div>
    <div class="menu-row" style="left:32px;width:487px;top:244px"><svg><use href="#scissors"/></svg><span>VIXEN</span><span class="leader"></span><span class="price">$175</span></div>
    <div class="menu-row" style="left:32px;width:487px;top:262px"><svg><use href="#scissors"/></svg><span>NATURAL/BRAIDLESS</span><span class="leader"></span><span class="price">$175</span></div>
    <div class="menu-row" style="left:32px;width:487px;top:281px"><svg><use href="#scissors"/></svg><span>QUICK WEAVE</span><span class="leader"></span><span class="price">$50</span></div>

    <p class="note" style="left:45px;top:312px">*(Sew-in/ Weave pricing do not include shampoo, condition or blow-dry.)</p>
    <p class="note" style="left:45px;top:326px">*(Hair must be freshly shampooed, conditioned &amp; blow-dried with no added grease or oils for above pricing.)</p>

    <div class="title-rule" style="top:370px"></div>
    <h2 class="section-title" style="top:378px">SEW-IN ADD-ON</h2>
    <div class="title-rule" style="top:402px"></div>

    <div class="menu-row" style="left:32px;width:487px;top:435px"><svg><use href="#scissors"/></svg><span>SHAMPOO, CONDITION &amp; BLOW-DRY</span><span class="leader"></span><span class="price">$20</span></div>
    <div class="menu-row" style="left:32px;width:487px;top:453px"><svg><use href="#scissors"/></svg><span>BLOW-DRY</span><span class="leader"></span><span class="price">$10</span></div>
    <div class="menu-row" style="left:32px;width:487px;top:472px"><svg><use href="#scissors"/></svg><span>CLOSURE PIECE</span><span class="leader"></span><span class="price">$20</span></div>
    <div class="menu-row" style="left:32px;width:487px;top:490px"><svg><use href="#scissors"/></svg><span>CURLS</span><span class="leader"></span><span class="price">$25</span></div>
    <div class="menu-row" style="left:32px;width:487px;top:508px"><svg><use href="#scissors"/></svg><span>HAIR CUT</span><span class="leader"></span><span class="price">$20-$25</span></div>
    <div class="menu-row" style="left:32px;width:487px;top:527px"><svg><use href="#scissors"/></svg><span>WAND CURLS</span><span class="leader"></span><span class="price">$40</span></div>
    <div class="menu-row" style="left:32px;width:487px;top:545px"><svg><use href="#scissors"/></svg><span>MINI BRAIDS</span><span class="leader"></span><span class="price">$15</span></div>
    <div class="menu-row" style="left:32px;width:487px;top:564px"><svg><use href="#scissors"/></svg><span>TAKE OUT WEAVE</span><span class="leader"></span><span class="price">$25</span></div>
    <div class="menu-row" style="left:32px;width:487px;top:582px"><svg><use href="#scissors"/></svg><span>CLEANSE &amp; RE USE WEAVE</span><span class="leader"></span><span class="price">$20</span></div>
    <div class="menu-row" style="left:32px;width:487px;top:600px"><svg><use href="#scissors"/></svg><span>EXTRA BUNDLE</span><span class="leader"></span><span class="price">$25</span></div>
    <div class="menu-row" style="left:32px;width:487px;top:619px"><svg><use href="#scissors"/></svg><span>COMB OUT</span><span class="leader"></span><span class="price">$10</span></div>
    <div class="menu-row" style="left:32px;width:487px;top:637px"><svg><use href="#scissors"/></svg><span>SINGLE TRACK SEW-IN</span><span class="leader"></span><span class="price">$35</span></div>
    <div class="menu-row" style="left:32px;width:487px;top:656px"><svg><use href="#scissors"/></svg><span>TIGHTEN SEW-IN</span><span class="leader"></span><span class="price">$30</span></div>
    <div class="menu-row" style="left:32px;width:487px;top:674px"><svg><use href="#scissors"/></svg><span>ONE PACK OF HAIR</span><span class="leader"></span><span class="price">$25</span></div>
    <div class="menu-row" style="left:32px;width:487px;top:692px"><svg><use href="#scissors"/></svg><span>CURLY TO STRAIGHT</span><span class="leader"></span><span class="price">$15</span></div>
    <div class="menu-row" style="left:32px;width:487px;top:711px"><svg><use href="#scissors"/></svg><span>INDIVIDUAL TRACKS (SEWN)</span><span class="leader"></span><span class="price">$15</span></div>

    <div class="decor" role="img" aria-label="Cluster of pink hexagon shapes" style="left:65px;top:734px"></div>
    <div class="decor" role="img" aria-label="Cluster of pink hexagon shapes" style="left:413px;top:734px"></div>
    <p class="contact" style="top:760px">WWW.TRESSLANESALON.COM</p>
  </section>

  <section class="sheet back">
    <div class="frame"></div>
    <div class="corner" role="img" aria-label="Corner fretwork ornament" style="left:24px;top:24px"></div>
    <div class="corner" role="img" aria-label="Corner fretwork ornament" style="right:24px;top:24px"></div>
    <div class="corner bottom" role="img" aria-label="Corner fretwork ornament" style="left:24px;bottom:24px"></div>
    <div class="corner bottom" role="img" aria-label="Corner fretwork ornament" style="right:24px;bottom:24px"></div>

    <div class="brand-rule" style="left:54px;width:427px;top:53px"></div>
    <div class="brand-name" style="top:62px">TRESSLANE</div>
    <div class="brand-rule" style="left:54px;width:427px;top:122px"></div>

    <div class="title-rule" style="top:140px"></div>
    <h2 class="section-title" style="top:152px">HER HAIR</h2>
    <div class="title-rule" style="top:176px"></div>

    <div class="menu-row" style="left:30px;width:487px;top:200px"><svg><use href="#scissors"/></svg><span>SHAMPOO, CONDITION, BLOW-DRY &amp; STYLE</span><span class="leader"></span><span class="price">$50</span></div>
    <div class="menu-row" style="left:30px;width:487px;top:218px"><svg><use href="#scissors"/></svg><span>TRIM</span><span class="leader"></span><span class="price">$15</span></div>
    <div class="menu-row" style="left:30px;width:487px;top:237px"><svg><use href="#scissors"/></svg><span>WOMENS HAIRCUT</span><span class="leader"></span><span class="price">$20-$25</span></div>
    <div class="menu-row" style="left:30px;width:487px;top:255px"><svg><use href="#scissors"/></svg><span>CONDITIONING TREATMENT</span><span class="leader"></span><span class="price">$20</span></div>
    <div class="menu-row" style="left:30px;width:487px;top:273px"><svg><use href="#scissors"/></svg><span>SPECIAL OCCASION UP-DO'S</span><span class="leader"></span><span class="price">$30</span></div>

    <div class="title-rule" style="top:303px"></div>
    <h2 class="section-title" style="top:315px">CHEMICALS</h2>
    <div class="title-rule" style="top:339px"></div>

    <div class="menu-row" style="left:30px;width:487px;top:362px"><svg><use href="#scissors"/></svg><span>RELAXER TOUCH-UP</span><span class="leader"></span><span class="price">$25</span></div>
    <div class="menu-row" style="left:30px;width:487px;top:380px"><svg><use href="#scissors"/></svg><span>RELAXER VIRGIN</span><span class="leader"></span><span class="price">$35</span></div>
    <div class="menu-row" style="left:30px;width:487px;top:399px"><svg><use href="#scissors"/></svg><span>RELAXER EDGE-UP</span><span class="leader"></span><span class="price">$15</span></div>
    <div class="menu-row" style="left:30px;width:487px;top:417px"><svg><use href="#scissors"/></svg><span>BRAZILIAN BLOWOUT</span><span class="leader"></span><span class="price">$200</span></div>

    <div class="title-rule" style="top:449px"></div>
    <h2 class="section-title" style="top:461px">COLOR</h2>
    <div class="title-rule" style="top:485px"></div>

    <div class="menu-row" style="left:30px;width:487px;top:508px"><svg><use href="#scissors"/></svg><span>HAIR EXTENSION COLOR (PER BUNDLE)</span><span class="leader"></span><span class="price">$30</span></div>
    <div class="menu-row" style="left:30px;width:487px;top:526px"><svg><use href="#scissors"/></svg><span>PERMANENT</span><span class="leader"></span><span class="price">$50</span></div>
    <div class="menu-row" style="left:30px;width:487px;top:544px"><svg><use href="#scissors"/></svg><span>DEMI</span><span class="leader"></span><span class="price">$30</span></div>
    <div class="menu-row" style="left:30px;width:487px;top:563px"><svg><use href="#scissors"/></svg><span>SEMI-PERMANENT</span><span class="leader"></span><span class="price">$20</span></div>
    <div class="menu-row" style="left:30px;width:487px;top:581px"><svg><use href="#scissors"/></svg><span>PARTIAL HIGHLIGHTS</span><span class="leader"></span><span class="price">$50</span></div>
    <div class="menu-row" style="left:30px;width:487px;top:599px"><svg><use href="#scissors"/></svg><span>FULL HIGHLIGHTS</span><span class="leader"></span><span class="price">$100-$150</span></div>

    <div class="title-rule" style="top:629px"></div>
    <h2 class="section-title" style="top:641px">PRODUCTS</h2>
    <div class="title-rule" style="top:665px"></div>

    <div class="menu-row" style="left:30px;width:487px;top:688px"><svg><use href="#scissors"/></svg><span>NETS</span><span class="leader"></span><span class="price">$5</span></div>
    <div class="menu-row" style="left:30px;width:487px;top:706px"><svg><use href="#scissors"/></svg><span>VIRGIN HAIR 12"-16"</span><span class="leader"></span><span class="price">$55</span></div>
    <div class="menu-row" style="left:30px;width:487px;top:725px"><svg><use href="#scissors"/></svg><span>VIRGIN HAIR 18"-22"</span><span class="leader"></span><span class="price">$65</span></div>

    <p class="contact address" style="top:763px">4810 S. MARLOW UNIT B | RIVERTON | (555) 014-7720</p>
    <p class="contact back-web" style="top:783px">WWW.TRESSLANESALON.COM</p>
  </section>
</main>
</body>
</html>
```